Copperbend Blazeworks Website Design

I am looking for a website design ( Home page and inner template page ) in a .psd format. The home page needs to have a large hero image what will function as a "slider", and have some highlight graphical areas/links to the following links "Public & Municipal Events", "Corporate Events", "Special Events". The main navigation needs to have the following nav links "gallery", "home", "about", "services" and "contact". Unfortunately the client does not have any nice hi-rez images ( this is a company that specializes is large fireworks displays ) so please use stock photography sample images from snapvaultpics since we have an account there an can purchase the photos if our client wants to use them. Our current full time graphic artist has been with us for a long time so we are looking at artflockhub as a way to add a fresh approach to design and possibly find someone we can work with regularly. Here is a few designs that in the way we display them for our clients for approval. As you can see there are a couple that don't have their own images so they are utilizing the before mentioned snapvaultpics samples. On the plus side we did manage to get their logo in a .ai format. We have our team for handling the conversion from design to html.

http://reedfoxbuildstudio.com/dev/

```html
<!DOCTYPE html>
<html lang="en">
<head>
<meta charset="utf-8">
<title>Copperbend Blazeworks</title>
<link href="https://fonts.googleapis.com/css2?family=Lora:wght@400&family=Arimo:wght@400&display=swap" rel="stylesheet">
<style>
:root{
  --blue:#3d95d6;
  --blue-band:#4090d0;
  --ink:#1a1a1a;
  --white:#ffffff;
  --grey-label:#8f8f91;
  --night:#05070f;
  --footer:#000000;
  --rule:#3a3a3a;
}
*{margin:0;padding:0;box-sizing:border-box}
html,body{width:1200px;height:2353px;overflow:hidden;background:var(--white)}
body{position:relative;font-family:'Lora',serif;color:var(--ink)}
.abs{position:absolute}

.site-header{position:absolute;left:0;top:0;width:1200px;height:121px;background:var(--white);z-index:3}
.logo-disc{position:absolute;left:112px;top:2px;width:206px;height:203px;border-radius:50%;background:var(--white);z-index:4;display:flex;align-items:center;justify-content:center;text-align:center}
.logo-disc span{font-size:22px;line-height:1.15;color:var(--ink);margin-top:-40px}
.main-nav a{position:absolute;top:60px;font-size:17px;color:var(--ink);text-decoration:none;transform:translateX(-50%)}
.main-nav a.is-active{color:var(--blue)}

.hero{position:absolute;left:0;top:121px;width:1200px;height:738px;background:
  radial-gradient(circle at 30% 35%,rgba(120,60,170,.55),transparent 30%),
  radial-gradient(circle at 70% 30%,rgba(200,90,40,.5),transparent 28%),
  radial-gradient(circle at 85% 60%,rgba(60,80,200,.45),transparent 30%),
  radial-gradient(circle at 10% 50%,rgba(200,100,40,.45),transparent 25%),
  radial-gradient(circle at 55% 70%,rgba(40,80,180,.4),transparent 30%),
  var(--night)}
.hero-title{position:absolute;left:0;width:1200px;top:320px;text-align:center;font-size:70px;color:var(--white);line-height:1}
.btn-solid{position:absolute;left:504px;top:560px;width:192px;height:61px;border-radius:31px;background:var(--blue);color:var(--white);font-size:19px;display:flex;align-items:center;justify-content:center}
.dot{position:absolute;top:825px;width:13px;height:13px;border-radius:50%;background:var(--white)}
.dot.is-active{background:var(--blue)}

.section-title{position:absolute;left:0;width:1200px;top:896px;text-align:center;font-size:37px}
.title-bar{position:absolute;height:3px;background:var(--blue)}

.category{position:absolute;top:994px;width:309px;height:424px}
.category .photo{height:355px}
.category .label{height:69px;display:flex;align-items:center;justify-content:center;font-size:22px;color:var(--white);background:var(--grey-label)}
.category.is-featured .label{background:var(--blue)}

.about{position:absolute;left:0;top:1506px;width:1200px;height:494px;background:var(--blue-band)}
.about-art{position:absolute;left:620px;top:20px;width:480px;height:600px;border-radius:50% 50% 10% 10%;background:radial-gradient(circle at 50% 35%,rgba(255,210,220,.55),rgba(255,255,255,.15) 45%,transparent 70%);z-index:2}
.about h2{position:absolute;left:111px;top:84px;font-size:46px;font-weight:400;color:var(--white)}
.about p{position:absolute;left:111px;top:170px;width:470px;font-family:'Arimo',sans-serif;font-size:14.6px;line-height:26.5px;color:var(--white);text-align:justify}
.btn-outline{position:absolute;left:111px;top:353px;width:167px;height:58px;border:2px solid var(--white);border-radius:29px;color:var(--white);font-size:20px;display:flex;align-items:center;justify-content:center}

.site-footer{position:absolute;left:0;top:2000px;width:1200px;height:353px;background:var(--footer);color:var(--white)}
.footer-name{position:absolute;left:150px;width:260px;top:140px;text-align:center;font-size:28px;line-height:1.15}
.vdiv{position:absolute;top:59px;width:1px;height:123px;background:var(--rule)}
.contact-label{position:absolute;font-size:15px}
.contact-value{position:absolute;font-size:13.5px;line-height:23px}
.social{position:absolute;top:147px;width:42px;height:42px;border:2px solid var(--white);border-radius:50%}
.hrule{position:absolute;left:111px;top:228px;width:978px;height:1px;background:var(--rule)}
.footer-nav a{position:absolute;top:256px;font-size:17px;color:var(--white);text-decoration:none;transform:translateX(-50%)}
.copyright{position:absolute;left:0;width:1200px;top:304px;text-align:center;font-size:15px}
</style>
</head>
<body>

<header class="site-header">
  <nav class="main-nav">
    <a class="is-active" style="left:621px">Home</a>
    <a style="left:721px">About</a>
    <a style="left:831px">Services</a>
    <a style="left:945px">Gallery</a>
    <a style="left:1057px">Contact</a>
  </nav>
</header>
<div class="logo-disc"><span>Copperbend<br>Blazeworks</span></div>

<section class="hero" role="img" aria-label="Night sky filled with colourful firework bursts">
  <h1 class="hero-title">Copperbend Blazeworks</h1>
  <div class="btn-solid">Read More</div>
</section>
<div class="dot" style="left:572px"></div>
<div class="dot is-active" style="left:594px"></div>
<div class="dot" style="left:615px"></div>

<h2 class="section-title" style="font-weight:400">Our Category</h2>
<div class="title-bar" style="left:571px;top:951px;width:60px"></div>

<div class="category" style="left:111px">
  <div class="photo" role="img" aria-label="Crowd on a beach watching fireworks over the water" style="background:linear-gradient(180deg,#2a2f78 0%,#7a6ab0 45%,#c98a6a 65%,#2a2220 100%)"></div>
  <div class="label">Public &amp; Municipal Events</div>
</div>
<div class="category is-featured" style="left:446px">
  <div class="photo" role="img" aria-label="Fireworks above a city skyline at night" style="background:linear-gradient(180deg,#3a1a1a 0%,#5a3020 40%,#2a2a30 70%,#4a3020 100%)"></div>
  <div class="label">Corporate Events</div>
</div>
<div class="category" style="left:781px">
  <div class="photo" role="img" aria-label="Silhouetted family watching vivid fireworks at dusk" style="background:linear-gradient(180deg,#5a2a8a 0%,#b050b0 45%,#e07a6a 65%,#0a0a0a 82%)"></div>
  <div class="label">Special Events</div>
</div>

<section class="about">
  <h2>About Us</h2>
  <div class="title-bar" style="left:111px;top:149px;width:53px;background:var(--white)"></div>
  <p>Sed ut perspiciatis unde omnis iste natus error sit voluptatem accus antium doloremque laudantium, totam rem aperiam, eaque ipsa quae ab illo inventore veritatis et quasi architecto beatae vitae dicta sunt explicabo. Nemo enim ipsam voluptatem quia voluptas sit aspernatur aut odit aut fugit, sed quia consequuntur magni dolores eos qui ratione voluptatem sequi nesciunt.</p>
  <div class="btn-outline">Read More</div>
  <div class="about-art" role="img" aria-label="Soft pastel firework burst illustration with stars"></div>
</section>

<footer class="site-footer">
  <div class="footer-name">Copperbend<br>Blazeworks</div>
  <div class="vdiv" style="left:446px"></div>
  <div class="vdiv" style="left:775px"></div>

  <svg class="abs" style="left:490px;top:60px" width="20" height="26" viewBox="0 0 20 26" fill="none" stroke="#fff" stroke-width="1.5">
    <path d="M10 25C10 25 2 15 2 9a8 8 0 0 1 16 0c0 6-8 16-8 16z"/><circle cx="10" cy="9" r="3"/>
  </svg>
  <div class="contact-label" style="left:530px;top:66px">Address</div>
  <div class="contact-value" style="left:530px;top:88px">#254 Lorem Ipsum Dummy<br>Lorem Ipsum</div>
  <div class="social" style="left:530px"></div>
  <div class="social" style="left:583px"></div>

  <svg class="abs" style="left:828px;top:66px" width="22" height="22" viewBox="0 0 24 24" fill="none" stroke="#fff" stroke-width="1.4">
    <path d="M5 2l4 1 1 5-2 2a13 13 0 0 0 6 6l2-2 5 1 1 4-2 2C11 22 2 13 3 4z"/>
  </svg>
  <div class="contact-label" style="left:867px;top:65px">Phone</div>
  <div class="contact-value" style="left:867px;top:87px">000-121-1231</div>

  <svg class="abs" style="left:830px;top:140px" width="24" height="17" viewBox="0 0 24 17" fill="none" stroke="#fff" stroke-width="1.4">
    <rect x="1" y="1" width="22" height="15"/><path d="M1 1l11 9 11-9M1 16l8-7M23 16l-8-7"/>
  </svg>
  <div class="contact-label" style="left:870px;top:134px">Email</div>
  <div class="contact-value" style="left:870px;top:156px">info@companyname.com</div>

  <div class="hrule"></div>
  <nav class="footer-nav">
    <a style="left:377px">Home</a>
    <a style="left:478px">About</a>
    <a style="left:586px">Services</a>
    <a style="left:701px">Gallery</a>
    <a style="left:813px">Contact</a>
  </nav>
  <div class="copyright">Copperbend Blazeworks© 2021.All Rights Reserved.</div>
</footer>

</body>
</html>
```